Brookvane Consulting Business Card Design

Business Card Design for Brookvane Consulting. Brookvane Consulting is a boutique consultancy based in Atlanta, GA., that specializes in marketing strategy, organization planning, and leadership development. We provide solutions for small businesses and startups as well as Vantage 300 companies.

http://brookvaneconsulting.com/

Target Market(s)

We provide solutions for small businesses and startups as well as Vantage 300 companies.

Industry/Entity Type

Consulting

Contact Information for Business Card

Two sided business card with priority on contact information, logo, tag line (Inspiration to Dream More, Do More, Become More)

Colors

Designer to choose colors to be used in the design.

Requirements
Must have
• contact information, logo, tag line (Inspiration to Dream More, Do More, Become More)
• Simple no over communication.
Nice to have
• I would like to see different placements of logo and creative use of both sides of the card
Should not have
• Do not put too much information on the card.

```html
<!DOCTYPE html>
<html lang="en">
<head>
<meta charset="utf-8">
<title>Brookvane Consulting Business Card</title>
<link rel="stylesheet" href="https://fonts.googleapis.com/css2?family=Jost:wght@300;400&family=Sorts+Mill+Goudy&display=swap">
<style>
  :root {
    --backdrop: #e4e4e4;
    --card-black: #030303;
    --curve-grey: #2a2a2a;
    --text-light: #d9d9d9;
    --text-muted: #bdbdbd;
    --logo-white: #ffffff;
    --back-glow: #3b3b3b;
    --tagline: #ececec;
  }
  * { margin: 0; padding: 0; box-sizing: border-box; }
  html, body { width: 1200px; height: 960px; overflow: hidden; }
  body { background: var(--backdrop); position: relative; font-family: "Jost", "Futura", sans-serif; }

  .card { position: absolute; width: 600px; height: 342px; overflow: hidden; }

  .card-front { left: 302px; top: 129px; background: var(--card-black); }
  .front-curve { position: absolute; inset: 0; }

  .holder-name {
    position: absolute; left: 52px; top: 70px;
    font-weight: 300; font-size: 40px; letter-spacing: 0.5px;
    color: var(--text-light); line-height: 1;
  }
  .holder-title {
    position: absolute; left: 59px; top: 121px;
    font-weight: 300; font-size: 15px; color: var(--text-muted);
  }
  .contact-list { position: absolute; left: 63px; top: 156px; list-style: none; }
  .contact-item {
    display: flex; align-items: center; gap: 8px;
    font-weight: 300; font-size: 14px; color: var(--text-muted);
    height: 19.5px;
  }
  .contact-icon { width: 13px; height: 13px; fill: var(--text-muted); }

  .brand-name {
    position: absolute; right: 32px; top: 262px;
    font-weight: 400; font-size: 26px; color: var(--logo-white);
    white-space: nowrap;
  }

  .card-back {
    left: 299px; top: 488px;
    background: radial-gradient(ellipse 60% 75% at 50% 20%, var(--back-glow) 0%, #151515 55%, #000 100%);
  }
  .tagline {
    position: absolute; left: 0; right: 0; top: 162px;
    text-align: center; font-family: "Sorts Mill Goudy", "Goudy Old Style", serif;
    font-size: 24px; line-height: 34px; color: var(--tagline);
  }
</style>
</head>
<body>
  <section class="card card-front" aria-label="Business card front">
    <svg class="front-curve" viewBox="0 0 600 342" aria-hidden="true">
      <defs>
        <linearGradient id="curveShade" x1="0" y1="1" x2="1" y2="0">
          <stop offset="0" stop-color="#3a3a3a"/>
          <stop offset="0.6" stop-color="#262626"/>
          <stop offset="1" stop-color="#0c0c0c"/>
        </linearGradient>
      </defs>
      <path d="M0 342 L0 338 C250 300 428 210 428 0 L440 0 C444 200 300 320 0 342 Z" fill="url(#curveShade)"/>
      <path d="M440 0 C444 200 300 320 0 342 L600 342 L600 0 Z" fill="#080808"/>
    </svg>

    <h1 class="holder-name">DARNELL WHITCOMBE</h1>
    <p class="holder-title">Founder/Managing Director</p>
    <ul class="contact-list">
      <li class="contact-item">
        <svg class="contact-icon" viewBox="0 0 16 16" aria-hidden="true"><path d="M3.6 1.2l2.3 2.6-1.3 1.9c.9 2 2.5 3.6 4.5 4.6l1.9-1.3 2.6 2.3-1.3 2.3C7 13.4 2.6 9 1.3 2.5z"/></svg>
        <span>424-555-0192</span>
      </li>
      <li class="contact-item">
        <svg class="contact-icon" viewBox="0 0 16 16" aria-hidden="true"><path d="M1 3h14v10H1z M2 4.2v.6l6 4 6-4v-.6z" fill-rule="evenodd"/></svg>
        <span>darnell@brookvaneconsulting.com</span>
      </li>
      <li class="contact-item">
        <svg class="contact-icon" viewBox="0 0 16 16" aria-hidden="true"><circle cx="8" cy="8" r="7"/><path d="M4 5c2 0 2 2 4 2s1 3 0 4-1 3-2 3C5 12 3 10 4 5z M10 3c1 1 3 1 3 3-1 0-2-1-3-3z" fill="#000"/></svg>
        <span>brookvaneconsulting.com</span>
      </li>
    </ul>

    <p class="brand-name">Brookvane Consulting</p>
  </section>

  <section class="card card-back" aria-label="Business card back">
    <p class="tagline">Inspiration to Dream More<br>Do More, Become More</p>
  </section>
</body>
</html>
```